Book Cover Design for Amber Lanterns Waiting: Notes on Mending When a Dear Friend Has Gone Too Soon

I need a book cover jacket design for a new book called Amber Lanterns Waiting: Notes on Mending When a Dear Friend Has Gone Too Soon.
The subject of the book is how to find balance again in your life after the suicide loss of a loved-one. I want the cover design to be in dark shades (browns, gray, variant shades) with lighter fonts for the title and for author's name. Would like to see designs with a concept of a dark tunnel with a road, a person walking down it, and a light ahead (off in the far distance) or an ominous picture of a road/journey with a person walking through the darkness. I need the final design to convey the message of journey through darkness to hope & healing.

Target Market(s)

men and women between the ages of 21-60.

Industry/Entity Type

Health And Wellness

Font styles to use
Serif
Sans Serif

Requirements
Must have
• Design must have a road or tunnel or both and a person walking towards it. It must convey a person walking into a heavy storm (sorrow), the other 1/4 to 1/2 of the book to convey hope, hopefulness, and brighter feeling, relief.
• My name at the bottom front- by Marisol Pendleby
Nice to have
• Some ideas I'd like to see:
• - Design idea to include road or tunnel. 3/4 of the book dark, ominous like storms, rain, fog, tears and convey sadness and deep sorrow; the other 1/4 of the book very light, peaceful, healing, less harsh and convey hope and positive progress ahead.
• Colors to Play with: Browns, Naturals, Grays, Darker-scale muted tones of blue
Should not have
• no red of any kind.

```html
<!DOCTYPE html>
<html lang="en">
<head>
<meta charset="utf-8">
<title>Amber Lanterns Waiting — Book Jacket</title>
<link rel="stylesheet" href="https://fonts.googleapis.com/css2?family=Arimo:wght@400&family=Questrial&display=swap">
<style>
  :root {
    --jacket: #231f20;
    --ink-light: #ffffff;
    --gold: #cdb07f;
    --photo-cool: #6f93b5;
    --photo-warm: #b8a27c;
  }
  * { margin: 0; padding: 0; box-sizing: border-box; }
  html, body { width: 1200px; height: 927px; overflow: hidden; background: var(--jacket); }
  .jacket { position: relative; width: 1200px; height: 927px; background: var(--jacket); }

  .back-subtitle, .front-subtitle {
    position: absolute; font-family: "Arimo", Arial, sans-serif; font-weight: 400; color: var(--gold);
    font-size: 28px; line-height: 39px; text-align: center;
  }
  .back-subtitle { left: 30px; width: 515px; top: 39px; }
  .back-blurb {
    position: absolute; left: 49px; top: 134px; width: 474px;
    font-family: "Arimo", Arial, sans-serif; color: var(--ink-light);
    font-size: 17.2px; line-height: 23.6px; text-align: justify;
  }
  .barcode-space { position: absolute; left: 321px; top: 720px; width: 202px; height: 131px; background: var(--ink-light); }

  .spine-title, .spine-author {
    position: absolute; writing-mode: vertical-rl; transform: rotate(180deg);
    color: var(--ink-light); text-align: center; white-space: nowrap;
  }
  .spine-title { left: 577px; top: 60px; width: 50px; height: 430px; font-family: "Questrial", "Century Gothic", sans-serif; font-size: 38px; line-height: 50px; }
  .spine-author { left: 577px; top: 572px; width: 50px; height: 284px; font-family: "Arimo", Arial, sans-serif; font-size: 38px; line-height: 50px; }

  .front-title {
    position: absolute; left: 640px; width: 548px; top: 56px; text-align: center;
    font-family: "Questrial", "Century Gothic", sans-serif; font-weight: 400; color: var(--ink-light);
    font-size: 46px; line-height: 60px; white-space: nowrap;
  }
  .cover-image { position: absolute; left: 638px; top: 186px; width: 550px; height: 318px; }
  .front-subtitle { left: 640px; width: 548px; top: 548px; }
  .front-author {
    position: absolute; left: 640px; width: 548px; top: 824px; text-align: center;
    font-family: "Arimo", Arial, sans-serif; color: var(--ink-light); font-size: 46px; line-height: 56px;
  }
</style>
</head>
<body>
<main class="jacket">
  <section class="back-cover">
    <h2 class="back-subtitle">Notes on Mending When a Dear<br>Friend Has Gone Too Soon</h2>
    <p class="back-blurb">Lorem ipsum dolor sit amet, consectetur adipisicing elit, sed do eiusmod tempor incididunt ut labore et dolore magna aliqua. Ut enim ad minim veniam, quis nostrud exercitation ullamco laboris nisi ut aliquip ex ea commodo consequat. Duis aute irure dolor in reprehenderit in voluptate velit esse cillum dolore eu fugiat nulla pariatur. Excepteur sint occaecat cupidatat non proident, sunt in culpa qui officia deserunt mollit anim id est laborum. Sed ut perspiciatis unde omnis iste natus error sit voluptatem accusantium doloremque laudantium, totam rem aperiam, eaque ipsa quae ab illo inventore veritatis et quasi architecto beatae vitae dicta sunt explicabo. Nemo enim ipsam voluptatem quia voluptas sit aspernatur aut odit aut fugit, sed quia consequuntur magni dolores eos qui ratione voluptatem sequi nesciunt. Neque porro quisquam est, qui dolorem ipsum quia dolor sit amet, consectetur, adipisci velit, sed quia non numquam eius modi tempora incidunt ut labore et dolore magnam aliquam quaerat voluptatem.</p>
    <div class="barcode-space"></div>
  </section>

  <section class="spine">
    <div class="spine-title">Amber Lanterns Waiting</div>
    <div class="spine-author">Marisol Pendleby</div>
  </section>

  <section class="front-cover">
    <h1 class="front-title">Amber Lanterns Waiting</h1>
    <svg class="cover-image" viewBox="0 0 550 318" role="img" aria-label="Cover photograph: sunlight breaking through storm clouds over the sea, in a torn-edge frame">
      <defs>
        <linearGradient id="photoTone" x1="0" y1="0" x2="0" y2="1">
          <stop offset="0" stop-color="var(--photo-cool)"/>
          <stop offset="1" stop-color="var(--photo-warm)"/>
        </linearGradient>
      </defs>
      <path fill="url(#photoTone)" d="M70 30 L95 22 L120 28 L150 18 L180 24 L215 14 L250 22 L270 8 L300 16 L330 4 L360 12 L395 2 L430 10 L455 20 L480 16 L500 30 L520 48 L532 70 L528 92 L540 112 L548 140 L542 165 L550 190 L538 210 L544 240 L530 262 L536 285 L515 300 L490 296 L460 310 L420 304 L380 314 L340 306 L300 316 L262 308 L225 312 L190 300 L150 296 L115 286 L80 280 L48 262 L30 240 L12 225 L18 200 L4 175 L10 150 L0 128 L14 110 L22 86 L40 70 L38 50 Z"/>
    </svg>
    <h2 class="front-subtitle">Notes on Mending When a Dear<br>Friend Has Gone Too Soon</h2>
    <p class="front-author">Marisol Pendleby</p>
  </section>
</main>
</body>
</html>
```